brightquokka.net we need a webpage designed for our new product

We need a webpage designed for our new range of products from our new brand. We have had a logo designed on sketchharbor (see attached) and we want to keep to this theme. Our first product is a range of affordable app controlled LED lightbulbs.

I have added some photos that we think is good inspirational material and would be good as a background to this website, but we want the site to look modern but not conventional. We would like something that makes our company look quirky not corporate.

Thats it

Target Market(s)

Our product is being stocked by big name online retailers in the UK, the page will get link through hits from our app. Our target market is gadget freaks of all ages.

Industry/Entity Type

It Company

Requirements
Must have
• We are going to need a help page, text to be uploaded next few days.

We need a contact page.

design my work on iOS and Android as most people will access page through their handset or tablet.
Should not have
• We do not want anything too corporate.

```html
<!DOCTYPE html>
<html lang="en">
<head>
<meta charset="utf-8">
<title>brightquokka</title>
<link href="https://fonts.googleapis.com/css2?family=Open+Sans:wght@300;400;600;700&family=Roboto:wght@400;500;700&display=swap" rel="stylesheet">
<style>
:root{
  --green:#3daa3a;
  --green-dark:#2a8f2a;
  --page:#ececec;
  --panel:#ffffff;
  --ink:#333333;
  --muted:#6f6f6f;
  --soft:#efefef;
  --nav-dark:#4a4a4a;
}
*{box-sizing:border-box;margin:0;padding:0}
html,body{width:973px;height:1200px;overflow:hidden}
body{background:var(--page);font-family:"Open Sans",sans-serif;color:var(--ink);position:relative}
.abs{position:absolute}
.topbar{left:0;top:0;width:973px;height:4px;background:var(--green)}
.search{left:92px;top:15px;width:165px;height:28px;background:#fff;border:1px solid #e2e2e2;font-size:10px;color:#aaa;padding:7px 8px}
.search svg{position:absolute;right:8px;top:7px}
.lang{left:741px;top:25px;font-size:10.5px;color:#777}
.flag{top:27px;width:14px;height:10px}
.panel{background:var(--panel);left:89px;width:795px}
.header{top:61px;height:115px}
.brand{left:118px;top:80px;width:110px;text-align:center}
.brand-dot{width:40px;height:40px;border-radius:50%;background:var(--green);margin:0 auto 12px}
.brand-name{font-size:9.5px;font-weight:700;color:var(--green);letter-spacing:.5px}
.call{left:700px;top:80px;font-size:18px;font-weight:300;color:#444;display:flex;align-items:center;gap:3px}
.nav{left:401px;top:122px;height:34px;display:flex;background:var(--green);border-radius:2px;overflow:hidden}
.nav a{display:flex;align-items:center;justify-content:center;font-size:11px;color:#fff;text-decoration:none;border-left:1px solid rgba(255,255,255,.25)}
.nav a.active{background:var(--nav-dark);border-left:none}
.hero-panel{top:176px;height:363px}
.hero{left:97px;top:186px;width:778px;height:344px;background:linear-gradient(135deg,#6b4a2e 0%,#a0522d 35%,#c9a36a 55%,#b03a2e 75%,#5a3a28 100%)}
.hero-box{left:97px;top:312px;width:363px;height:120px;background:rgba(0,0,0,.72);padding:14px 24px 0 26px}
.hero-box h1{font-size:19px;font-weight:300;color:#fff;margin-bottom:9px}
.hero-box h1 b{font-weight:600}
.hero-box p{font-size:10px;line-height:13px;color:#8d8d8d}
.content{top:553px;height:414px}
.tile{top:560px;width:254px;height:132px}
.tile .cap{position:absolute;left:0;bottom:0;width:100%;height:29px;background:rgba(255,255,255,.55);font-size:13.5px;color:#333;padding:5px 8px}
.welcome-h{left:103px;top:732px;font-size:21px;font-weight:300;color:#444}
.welcome-p{left:103px;top:770px;width:355px;font-size:10.4px;line-height:17px;font-weight:300;color:#555}
.btn{left:105px;top:905px;width:87px;height:32px;background:linear-gradient(#3fb23c,var(--green-dark));color:#fff;font-size:10.5px;display:flex;align-items:center;justify-content:center;border-radius:2px}
.say-h{left:533px;top:736px;font-size:16.5px;font-weight:300;color:#444}
.arrow{top:733px;width:25px;height:25px;background:#ececec;border:1px solid #e0e0e0;display:flex;align-items:center;justify-content:center}
.quote{left:518px;top:769px;width:357px;height:91px;background:var(--soft);padding:16px 14px 0 27px;font-size:10.4px;line-height:14px;color:#555}
.quote-mark{left:532px;top:770px;font-size:20px;font-style:italic;font-weight:700;color:var(--green)}
.avatar{left:531px;top:877px;width:56px;height:56px;border-radius:50%;background:radial-gradient(circle,#e8c9ae,#c9a07e);border:3px solid #eee}
.name{left:602px;top:887px;font-family:"Roboto",sans-serif;font-size:13.5px;font-weight:500;color:#333}
.city{left:602px;top:905px;font-family:"Roboto",sans-serif;font-size:11.5px;color:#777}
.footer{top:980px;height:162px}
.f-h{top:1000px;font-size:12px;font-weight:700;color:#222;font-family:"Roboto",sans-serif}
.links{left:121px;top:1019px;list-style:none;font-size:10.5px;line-height:17px;color:#222}
.news-p{left:289px;top:1024px;width:155px;font-family:"Roboto",sans-serif;font-size:8px;line-height:9.8px;color:#9a9a9a;letter-spacing:.4px}
.input{left:289px;top:1075px;width:154px;height:23px;border:1px solid #ccc;background:#f6f6f6;border-radius:2px;font-size:9.5px;font-style:italic;color:#777;padding:5px 7px;font-family:"Roboto",sans-serif}
.subscribe{left:292px;top:1104px;font-family:"Roboto",sans-serif;font-size:10px;font-weight:700;color:#222}
.social{left:566px;top:1029px;list-style:none;font-family:"Roboto",sans-serif;font-size:10px;color:#555}
.social li{display:flex;align-items:center;gap:8px;height:20px}
.social i{display:block;width:12px;height:12px;border-radius:2px}
.badge{border-radius:2px}
.sec{font-family:"Roboto",sans-serif;font-weight:700;color:#333}
.copy{left:0;top:1165px;width:973px;text-align:center;font-size:10.5px;color:#222}
</style>
</head>
<body>
<div class="abs topbar"></div>

<div class="abs search">Search
  <svg width="13" height="13" viewBox="0 0 13 13"><circle cx="5.5" cy="5.5" r="4" fill="none" stroke="#3daa3a" stroke-width="2"/><line x1="8.5" y1="8.5" x2="12" y2="12" stroke="#3daa3a" stroke-width="2"/></svg>
</div>
<div class="abs lang">Select Language</div>
<svg class="abs flag" style="left:838px" viewBox="0 0 3 2"><rect width="1" height="2" fill="#1b3fa8"/><rect x="1" width="1" height="2" fill="#fff"/><rect x="2" width="1" height="2" fill="#e0262b"/></svg>
<svg class="abs flag" style="left:864px" viewBox="0 0 14 10"><rect width="14" height="10" fill="#1b3f8a"/><path d="M0 0L14 10M14 0L0 10" stroke="#fff" stroke-width="2"/><path d="M7 0V10M0 5H14" stroke="#fff" stroke-width="3"/><path d="M7 0V10M0 5H14" stroke="#d42a2a" stroke-width="1.5"/></svg>

<div class="abs panel header"></div>
<div class="abs brand"><div class="brand-dot"></div><div class="brand-name">BRIGHTQUOKKA</div></div>
<div class="abs call">
  <svg width="20" height="20" viewBox="0 0 20 20"><path d="M4 6c0 6 4 10 10 10l2-2-3-3-2 1c-2-1-3-2-4-4l1-2-3-3z" fill="none" stroke="#333" stroke-width="1.6"/></svg>
  Call: 020 4417 3082
</div>
<nav class="abs nav">
  <a class="active" style="width:59px">HOME</a>
  <a style="width:71px">About Us</a>
  <a style="width:63px">Services</a>
  <a style="width:49px">Store</a>
  <a style="width:67px">Buy Now</a>
  <a style="width:69px">Products</a>
  <a style="width:88px">Contact Us</a>
</nav>

<div class="abs panel hero-panel"></div>
<div class="abs hero" role="img" aria-label="Photo of a crowded vintage shop with toy pedal cars and superhero figures"></div>
<div class="abs hero-box">
  <h1>A big name online retailers in the <b>UK</b></h1>
  <p>It is a long established fact that a reader will be distracted by the readable content of a page when looking at its layout. The point of using Lorem Ipsum is that it has a more-or-less normal distribution of letters, as opposed to using 'Content here, content here,</p>
</div>

<div class="abs panel content"></div>
<div class="abs tile" style="left:99px;background:linear-gradient(#e6e6e2,#bdbdb6)" role="img" aria-label="Photo of LED lightbulbs"><div class="cap">LED lightbulbs</div></div>
<div class="abs tile" style="left:360px;background:linear-gradient(#a07a5c,#d8c7b4)" role="img" aria-label="Photo of a white ceramic seal figure"><div class="cap">Lorem Lipsum</div></div>
<div class="abs tile" style="left:621px;background:linear-gradient(#5a4a30,#d99a2a)" role="img" aria-label="Photo of orange cartoon cat figurines"><div class="cap">Lorem Lipsum</div></div>

<h2 class="abs welcome-h">Welcome to Our Website</h2>
<p class="abs welcome-p">It is a long established fact that a reader will be distracted by the readable content of a page when looking at its layout. The point of using Lorem Ipsum is that it has a more-or-less normal distribution of letters, as opposed to using 'Content here, content here', making it look like readable English. Many desktop publishing packages and web page editors now use Lorem Ipsum as their default model text, and a search for 'lorem ipsum' will uncover many web sites still in their infancy.</p>
<div class="abs btn">READ MORE</div>

<h2 class="abs say-h">WHAT OUR CUSTOMERS SAY</h2>
<div class="abs arrow" style="left:775px"><svg width="6" height="9"><path d="M5 1L1 4.5 5 8" fill="none" stroke="#555"/></svg></div>
<div class="abs arrow" style="left:802px"><svg width="6" height="9"><path d="M1 1L5 4.5 1 8" fill="none" stroke="#555"/></svg></div>
<div class="abs quote">It is a long established fact that a reader will be distracted by the readable content of a page when looking at its layout. The point of using Lorem Ipsum is that it has a more-or-less normal distribution of letters</div>
<div class="abs quote-mark">//</div>
<div class="abs avatar" role="img" aria-label="Customer portrait"></div>
<div class="abs name">Rosa Delling</div>
<div class="abs city">Los Angeles</div>

<div class="abs panel footer"></div>
<div class="abs f-h" style="left:121px;font-family:'Open Sans',sans-serif">Links</div>
<ul class="abs links"><li>Home</li><li>about us</li><li>services</li><li>help</li><li>contact us</li></ul>
<div class="abs f-h" style="left:289px">Newsletter</div>
<p class="abs news-p">Get all the latest information on fashion &amp; products and stay updated. Subscribe our newsletter now!</p>
<div class="abs input">Your Email Address</div>
<div class="abs subscribe">Subscribe &#9656;</div>
<div class="abs f-h" style="left:567px">Social Media</div>
<ul class="abs social">
  <li><i style="background:#3b5998"></i>Chatterbox</li>
  <li><i style="background:#c4302b"></i>Clipstream</li>
  <li><i style="background:#f26522"></i>RSS Feeds</li>
  <li><i style="background:#4fa9e0"></i>Tweetnest</li>
</ul>
<div class="abs badge" style="left:720px;top:1012px;width:26px;height:17px;background:#1a3f8f"></div>
<div class="abs badge" style="left:752px;top:1012px;width:26px;height:17px;background:#d9232d"></div>
<div class="abs badge" style="left:783px;top:1012px;width:26px;height:17px;background:#2e8fc9"></div>
<div class="abs badge" style="left:814px;top:1012px;width:26px;height:17px;background:#e9e9e9;border:1px solid #f08020"></div>
<div class="abs sec" style="left:724px;top:1041px;font-size:8px;line-height:8px;text-align:center;color:#666">Privacy<br>Guaranteed</div>
<div class="abs" style="left:778px;top:1040px;width:14px;height:18px;border-radius:3px 3px 7px 7px;background:#8fc46a"></div>
<div class="abs badge" style="left:803px;top:1041px;width:37px;height:19px;background:#f4c21f"></div>
<div class="abs sec" style="left:719px;top:1073px;font-size:7px;line-height:8px">100% Secure<br>128 SSL Encryption</div>
<div class="abs" style="left:798px;top:1076px;width:11px;height:10px;border:1px solid #888"></div>
<div class="abs" style="left:822px;top:1069px;width:18px;height:22px;border-radius:3px 3px 9px 9px;background:#5a3a1a"></div>

<div class="abs copy">© 2014 brightquokka. All rights reserved</div>
</body>
</html>
```